For Sale Sign for Real Estate Agency

We need a For Sale Sign designed for our agency. I want a very simple/elegant sign that says "For Sale" towards the top of the sign (not in huge letters). Most of the sign should be a design/picture with our name and phone number somewhere at the bottom.

One significant detail, it's important that our logo not be too big or the center piece of the sign. Since our company name has the word "rent" in it, people assume the house is for rent, instead of for sale.

I attached our logo and a rough outline of the format I'm looking for.

Again, I'm looking for elegant and simple! Thanks for your time

Industry/Entity Type

Real Estate

Colors

Designer to choose colors to be used in the design.

Requirements
Must have
Nice to have
Should not have
• Nothing tacky!
• Our logo/company name should not be too big or the center piece of the sign. Since our company name has the word "rent" in it, people assume the house is for rent, instead of for sale.

```html
<!DOCTYPE html>
<html lang="en">
<head>
<meta charset="utf-8">
<title>For Sale Sign</title>
<link rel="stylesheet" href="https://fonts.googleapis.com/css2?family=Poppins:wght@700&family=Barlow:wght@500;600&display=swap">
<style>
  :root {
    --backdrop: #3a414b;
    --sign-red: #ed1c24;
    --sign-white: #ffffff;
    --ink: #1d1d1f;
    --art-light: #fbeaea;
    --art-mid: #f3c9cb;
  }
  html, body {
    margin: 0;
    padding: 0;
    width: 1200px;
    height: 837px;
    overflow: hidden;
    background: var(--backdrop);
  }
  .canvas {
    position: relative;
    width: 1200px;
    height: 837px;
    display: flex;
    align-items: center;
    justify-content: center;
  }
  .sign {
    display: block;
    width: 360px;
    height: 752px;
  }
  .headline {
    font-family: "Poppins", sans-serif;
    font-weight: 700;
    font-size: 62px;
    fill: var(--sign-white);
    letter-spacing: 1px;
  }
  .agency-name {
    font-family: "Barlow", sans-serif;
    font-weight: 500;
    font-size: 24px;
    fill: var(--ink);
  }
  .phone {
    font-family: "Barlow", sans-serif;
    font-weight: 600;
    font-size: 34px;
    fill: var(--ink);
    letter-spacing: 1.5px;
  }
</style>
</head>
<body>
  <main class="canvas">
    <svg class="sign" viewBox="0 0 378 790" xmlns="http://www.w3.org/2000/svg">
      <defs>
        <linearGradient id="artFill" x1="0" y1="0" x2="0" y2="1">
          <stop offset="0" stop-color="var(--art-light)"/>
          <stop offset="1" stop-color="var(--art-mid)"/>
        </linearGradient>
      </defs>

      <rect class="sign-base" x="0" y="0" width="378" height="790" fill="var(--sign-white)"/>

      <path class="header-band" fill="var(--sign-red)"
            d="M0,0 H378 V288 C330,330 290,332 245,312 C190,288 140,240 80,248 C45,252 20,270 0,290 Z"/>
      <path class="header-swoosh" fill="none" stroke="var(--sign-white)" stroke-width="3" stroke-linecap="round"
            d="M72,246 C130,232 175,252 225,280 C265,302 295,312 325,310"/>

      <text class="headline" x="189" y="128" text-anchor="middle">FOR</text>
      <text class="headline" x="189" y="192" text-anchor="middle">SALE</text>

      <rect class="house-art" x="40" y="408" width="305" height="125" rx="10" fill="url(#artFill)"
            role="img" aria-label="Illustration of two house rooftops with a red check-mark roof on a curved ground line"/>

      <text class="agency-name" x="189" y="674" text-anchor="middle">HomeCrest Realty</text>
      <text class="phone" x="189" y="740" text-anchor="middle">555-310-477</text>
    </svg>
  </main>
</body>
</html>
```